Business Card for Coastal Tundrabridge Advisory

We need a business card for Coastal Tundrabridge Advisory. The company website address is provided below. The company logo is attached. We provide specialized permafrost services to the mining, transportation, and oil & gas industries. The card should be prepared for:
Matthias Korhonen, PhD.
Coastal Tundrabridge Advisory
PO Box 418259
Quillwater, Alaska 99642
Direct: +1-907-555-0143
Email: mkorhonen@tundrabridgeadvisory.example
Website: www.coastaltundrabridgeadvisory.example

```html
<!DOCTYPE html>
<html lang="en">
<head>
<meta charset="utf-8">
<title>Coastal Tundrabridge Advisory — Business Card</title>
<link rel="stylesheet" href="https://fonts.googleapis.com/css2?family=Montserrat:wght@400;500;700&display=swap">
<style>
  :root {
    --backdrop: #e9e6e1;
    --card-dark: #121a22;
    --card-light: #ffffff;
    --ink: #16191d;
    --ink-soft: #3b3f44;
    --on-dark: #ffffff;
  }
  * { box-sizing: border-box; margin: 0; padding: 0; }
  html, body {
    width: 1200px; height: 676px; overflow: hidden;
    background: var(--backdrop);
    font-family: "Montserrat", sans-serif;
  }
  .card-set {
    position: relative; width: 1200px; height: 676px;
  }
  .card {
    position: absolute; top: 198px;
    width: 500px; height: 286px;
    box-shadow: 0 10px 24px rgba(0,0,0,0.18);
  }
  .card--front {
    left: 80px; background: var(--card-dark);
    display: flex; align-items: center; justify-content: center;
  }
  .card--back {
    left: 620px; background: var(--card-light); color: var(--ink);
  }
  .brand-name {
    font-family: "Montserrat", sans-serif;
    font-weight: 700; text-transform: uppercase;
    letter-spacing: 0.06em; line-height: 1.15; text-align: left;
  }
  .card--front .brand-name { color: var(--on-dark); font-size: 25px; }
  .card--back .brand-name {
    position: absolute; left: 40px; top: 32px;
    color: var(--ink); font-size: 24px;
  }
  .holder {
    position: absolute; left: 40px; top: 124px;
  }
  .holder-name { font-size: 17px; font-weight: 700; }
  .holder-title { font-size: 10px; font-weight: 500; color: var(--ink-soft); margin-top: 3px; }
  .contact-list {
    position: absolute; left: 40px; top: 178px; list-style: none;
  }
  .contact-item {
    display: flex; align-items: center; gap: 9px;
    font-size: 10.5px; color: var(--ink-soft); margin-bottom: 8px;
  }
  .contact-icon { width: 11px; height: 11px; flex: none; }
  .mailing-address {
    position: absolute; right: 36px; bottom: 28px;
    font-size: 10.5px; line-height: 1.45; color: var(--ink-soft); font-style: normal;
  }
</style>
</head>
<body>
<main class="card-set">
  <section class="card card--front">
    <p class="brand-name">Coastal<br>Tundrabridge Advisory</p>
  </section>

  <section class="card card--back">
    <p class="brand-name">Coastal<br>Tundrabridge Advisory</p>

    <div class="holder">
      <p class="holder-name">Matthias Korhonen, PhD.</p>
      <p class="holder-title">Managing Director</p>
    </div>

    <ul class="contact-list">
      <li class="contact-item">
        <svg class="contact-icon" viewBox="0 0 24 24" aria-hidden="true"><path fill="#16191d" d="M6.6 10.8a15.2 15.2 0 0 0 6.6 6.6l2.2-2.2c.3-.3.7-.4 1-.2 1.1.4 2.3.6 3.6.6.6 0 1 .4 1 1V20c0 .6-.4 1-1 1A17 17 0 0 1 3 4c0-.6.4-1 1-1h3.5c.6 0 1 .4 1 1 0 1.3.2 2.5.6 3.6.1.3 0 .7-.2 1z"/></svg>
        <span>+1-907-555-0143</span>
      </li>
      <li class="contact-item">
        <svg class="contact-icon" viewBox="0 0 24 24" aria-hidden="true"><rect x="2" y="5" width="20" height="14" rx="2" fill="#16191d"/><path d="M3 6l9 7 9-7" fill="none" stroke="#fff" stroke-width="1.6"/></svg>
        <span>mkorhonen@tundrabridgeadvisory.example</span>
      </li>
      <li class="contact-item">
        <svg class="contact-icon" viewBox="0 0 24 24" aria-hidden="true"><circle cx="12" cy="12" r="9.5" fill="none" stroke="#16191d" stroke-width="2"/><ellipse cx="12" cy="12" rx="4" ry="9.5" fill="none" stroke="#16191d" stroke-width="1.6"/><path d="M2.5 12h19" stroke="#16191d" stroke-width="1.6"/></svg>
        <span>www.coastaltundrabridgeadvisory.example</span>
      </li>
    </ul>

    <address class="mailing-address">
      PO Box 418259<br>
      Quillwater, Alaska 99642
    </address>
  </section>
</main>
</body>
</html>
```